Build Distinctive Business Card: Public Relations Government Relations firm

I have logo and colors done (attached) need a very cool way to present it on a business card (can be two sided if need be).

Public Relations Government Relations firm

Info:

Paul Marchetti, CEO
Keystone Public Relations
2730 West Harlan Blvd.
Los Angeles CA 90012
(o) 213.555.0148
(f) 213.555.0173
paul@keystonekpr-example.com

Target Market(s)

Government relations, public relations, lobbyist, I was a past State Senator

Industry/Entity Type

Business

Contact Information for Business Card

Info:

Paul Marchetti, CEO
Keystone Public Relations
2730 West Harlan Blvd.
Los Angeles CA 90012
(o) 213.555.0148
(f) 213.555.0173
paul@keystonekpr-example.com
@paulmarchetti

Requirements
Must have
• A sense of balance given logo is already done.
• It's a government relations firm really.
• Lobbyist type.
• Senatorial type...

```html
<!DOCTYPE html>
<html lang="en">
<head>
<meta charset="utf-8">
<title>Keystone Public Relations — Business Card</title>
<link rel="stylesheet" href="https://fonts.googleapis.com/css2?family=Arimo:wght@400;700&display=swap">
<style>
  :root {
    --ink: #0b0b0b;
    --paper: #f4f4f4;
    --paper-edge: #e2e2e2;
    --white: #ffffff;
    --stage: #d9d9d9;
    --muted: #2a2a2a;
  }
  * { box-sizing: border-box; margin: 0; padding: 0; }
  html, body {
    width: 1200px; height: 885px; overflow: hidden;
    background: var(--stage);
    font-family: "Arimo", Arial, sans-serif;
  }
  .canvas {
    width: 1200px; height: 885px;
    display: flex; flex-direction: column;
    align-items: center; justify-content: center; gap: 56px;
  }
  .card {
    position: relative;
    width: 620px; height: 354px;
    border-radius: 20px;
    overflow: hidden;
    background: linear-gradient(180deg, var(--white), var(--paper) 70%, var(--paper-edge));
    box-shadow: 0 6px 18px rgba(0,0,0,0.18);
  }
  .band {
    position: absolute; left: 0; top: 0; right: 0;
    background: var(--ink);
  }
  .brand {
    display: flex; align-items: center; gap: 14px;
    color: var(--white);
  }
  .brand-mark {
    width: 62px; height: 62px; border-radius: 50%;
    border: 5px solid var(--white);
  }
  .brand-name {
    font-size: 40px; font-weight: 700; letter-spacing: -0.5px;
  }

  /* Front */
  .card-front .band { height: 158px; }
  .card-front .brand { position: absolute; left: 38px; top: 48px; }
  .holder {
    position: absolute; right: 40px; top: 52px;
    text-align: right; color: var(--white);
  }
  .holder-name { font-size: 27px; font-weight: 700; letter-spacing: -0.3px; }
  .holder-title { font-size: 13px; margin-top: 3px; }
  .address {
    position: absolute; right: 40px; top: 184px;
    text-align: right; font-size: 13.5px; line-height: 1.4; color: var(--muted);
  }
  .contacts {
    position: absolute; left: 40px; bottom: 34px;
    list-style: none; font-size: 14px; line-height: 1.45; color: var(--muted);
  }

  /* Back */
  .card-back .band { height: 178px; }
  .card-back .brand {
    position: absolute; left: 0; right: 0; top: 56px; justify-content: center;
  }
  .tagline {
    position: absolute; left: 0; right: 0; top: 246px;
    text-align: center; font-size: 27px; font-weight: 700; color: var(--ink);
  }
</style>
</head>
<body>
<main class="canvas">

  <section class="card card-front" aria-label="Business card, front">
    <div class="band"></div>
    <div class="brand">
      <span class="brand-mark" aria-hidden="true"></span>
      <span class="brand-name">Keystone</span>
    </div>
    <div class="holder">
      <div class="holder-name">Paul Marchetti</div>
      <div class="holder-title">CEO</div>
    </div>
    <address class="address" style="font-style:normal">
      A : 2730 West Harlan Blvd.<br>
      Los Angeles CA 90012
    </address>
    <ul class="contacts">
      <li>P : 213.555.0148</li>
      <li>P : 213.555.0173</li>
      <li>E : paul@keystonekpr-example.com</li>
    </ul>
  </section>

  <section class="card card-back" aria-label="Business card, back">
    <div class="band"></div>
    <div class="brand">
      <span class="brand-mark" aria-hidden="true"></span>
      <span class="brand-name">Keystone</span>
    </div>
    <p class="tagline">Keystone Public Relations</p>
  </section>

</main>
</body>
</html>
```